My new Bible based podcast needs a Podcast Cover Design for Plexora directory

I need a Podcast Cover Design design for my podcast listing in Plexora. The podcast is called Morning Lantern Calling Home. I would like something cheerful, warm, and fresh because I take a non-traditional approach to explaining how the Bible is relevant to people today. My goal is to get back to the original spirituality of the Bible without all the centuries of added man-made doctrines. It would be great to show a sense of peace and hope, with new possibilities. This is not like a floating corporate logo. I need it to be square and full color/design all the way to the edges.

I have resubmitted this project because I did not understand how to ask for a podcast cover design. If you already submitted for me, I apologize for not knowing how the system works. I did not give the best picture of what I needed.

Target Market(s)

People who want a fresh look at the Bible

Industry/Entity Type

Religious

Logo Text

Morning Lantern Calling Home

Colors

Designer to choose colors to be used in the design.

Requirements
Must have
• It must be square. The design should fill the space. See screen shot below of podcast cover designs on the Christianity/Spirituality page of Plexora directory so you can see where the podcast cover design needs to fit in and stand out.
• The final design will need to be:
• 3,000 x 3,000 pixels (but readable at 150 x 150)
• 72 dpi
• .jpg or .png format
• rgb color space
Nice to have
• Perhaps an open book suggesting the Bible, but not necessary.
Should not have
• No microphones or airwaves.

```html
<!DOCTYPE html>
<html lang="en">
<head>
<meta charset="utf-8">
<title>Morning Lantern Calling Home — Podcast Cover</title>
<link href="https://fonts.googleapis.com/css2?family=Cinzel:wght@400&display=swap" rel="stylesheet">
<style>
  :root {
    --parchment-light: #ece4c9;
    --parchment-mid: #d3c7a2;
    --parchment-dark: #a89a72;
    --band-dark: #2e2a28;
    --band-light: rgba(226, 220, 200, 0.55);
    --band-text: #eee8d5;
    --title-ink: #0e0c0a;
    --book-black: #151311;
    --book-edge: #2a2622;
  }
  html, body {
    margin: 0;
    padding: 0;
    width: 1200px;
    height: 1200px;
    overflow: hidden;
    background: var(--parchment-mid);
  }
  .cover {
    position: relative;
    width: 1200px;
    height: 1200px;
    overflow: hidden;
    font-family: "Cinzel", "Trajan Pro", serif;
  }
  .cover__photo {
    position: absolute;
    inset: 0;
    background:
      radial-gradient(ellipse at 55% 35%, var(--parchment-light) 0%, var(--parchment-mid) 55%, var(--parchment-dark) 100%);
  }
  .cover__book {
    position: absolute;
    left: 352px;
    top: 842px;
    width: 848px;
    height: 286px;
    border-radius: 10px 0 0 10px;
    background: linear-gradient(180deg, var(--book-edge) 0%, var(--book-black) 22%, var(--book-black) 100%);
  }
  .cover__table {
    position: absolute;
    left: 0;
    right: 0;
    top: 1128px;
    bottom: 0;
    background: linear-gradient(180deg, #3a3630 0%, #6d6555 100%);
  }
  .title-band {
    position: absolute;
    top: 66px;
    left: 0;
    width: 1200px;
    height: 196px;
    display: flex;
  }
  .title-band__dark {
    background: var(--band-dark);
    width: 640px;
    display: flex;
    align-items: center;
    padding-left: 34px;
    box-sizing: border-box;
  }
  .title-band__light {
    flex: 1;
    background: var(--band-light);
  }
  .title-band__word {
    color: var(--band-text);
    font-size: 112px;
    line-height: 1;
    letter-spacing: 2px;
    margin: 0;
  }
  .title-main {
    position: absolute;
    left: 0;
    right: 0;
    margin: 0;
    color: var(--title-ink);
    font-weight: 400;
    text-align: center;
    line-height: 1;
  }
  .title-main--lantern {
    top: 300px;
    font-size: 204px;
    letter-spacing: 6px;
  }
  .title-main--calling {
    top: 540px;
    font-size: 128px;
    letter-spacing: 2px;
  }
</style>
</head>
<body>
  <main class="cover">
    <div class="cover__photo" role="img" aria-label="Soft aged parchment backdrop behind a closed black leather Bible with gilt bands and a ribbon marker, resting on a table"></div>
    <div class="cover__book" role="img" aria-label="Closed black leather Bible lying on its side"></div>
    <div class="cover__table" role="img" aria-label="Dark reflective tabletop"></div>

    <div class="title-band">
      <div class="title-band__dark">
        <p class="title-band__word">MORNING</p>
      </div>
      <div class="title-band__light"></div>
    </div>

    <h1 class="title-main title-main--lantern">LANTERN</h1>
    <p class="title-main title-main--calling">CALLING HOME</p>
  </main>
</body>
</html>
```